vintage snapframe thank you postcard

I am wanting to use this postcard for my wedding thank you. My theme is: outdoor, rustic, country, vintage, neutral colored. The photo booth at my wedding was in a grain bin on a old victorian couch photos taken with a digital snapframe camera! I want the post card to look like an old fashioned snapframe picture with the border and all. At the bottom saying "thank you" or "Neil and Vera," "Bradwick Wedding", "June 14, 2014," something to that affect. On the back left side leaving room for me to write a personal message thanking them for the help/gift/support. The back right side left for the name and address. I will add a wedding picture of the two of us to the front (from our wedding day). Anything that gives the post card a vintage old time feeling is great!! I have a general idea of what I want but, now I know you guys can take care of the rest for me! :) thank you in advance!! -Vera

Target Market(s)

family, friends - all ages!

Industry/Entity Type

Wedding

Requirements
Must have
• "snapframe photo" look
vintage
"Thank you"
"Neil and Vera"
Nice to have
• June 14, 2014

```html
<!DOCTYPE html>
<html lang="en">
<head>
<meta charset="utf-8">
<title>Bradwick Wedding – Thank You Postcard</title>
<link rel="stylesheet" href="https://fonts.googleapis.com/css2?family=Great+Vibes&family=Handlee&family=Oswald:wght@300&display=swap">
<style>
  :root {
    --page: #ffffff;
    --wood-teal: #7fc4b0;
    --wood-teal-light: #a6dccb;
    --wood-mid: #4e7d6e;
    --wood-dark: #2f2a22;
    --vignette: #14110d;
    --frame-cream: #f3ecd9;
    --frame-edge: #d9ccb0;
    --photo-blush: #eaddd2;
    --photo-shade: #cdb8ad;
    --title-white: #ffffff;
    --caption: #7b6f5e;
    --footer-text: #d8d4cc;
    --back-paper: #f2f2f1;
    --back-line: #e6e6e4;
    --chevron: #dcdcda;
    --ink-purple: #5b3f95;
    --ink-purple-soft: #6e55a6;
    --flower-peach: 241, 214, 189;
    --stamp: #c9b8a3;
  }
  * { box-sizing: border-box; margin: 0; padding: 0; }
  html, body { width: 1200px; height: 463px; overflow: hidden; background: var(--page); }

  .postcard { position: relative; width: 1200px; height: 463px; }

  /* ---------- Front ---------- */
  .front {
    position: absolute; left: 0; top: 0; width: 598px; height: 463px; overflow: hidden;
    background: var(--vignette);
  }
  .front__scene {
    position: absolute; inset: 0;
    background: radial-gradient(ellipse 75% 70% at 50% 40%, var(--wood-teal-light) 0%, var(--wood-teal) 35%, var(--wood-mid) 62%, var(--wood-dark) 85%, var(--vignette) 100%);
  }
  .front__keepsake {
    position: absolute; left: 30px; top: 30px; width: 160px; height: 130px; border-radius: 50%;
    background: radial-gradient(ellipse at 60% 55%, #e8e4dc 0%, #b9b2ac 45%, rgba(150,140,150,0) 75%);
  }
  .front__title {
    position: absolute; left: 250px; top: 30px; width: 260px;
    font-family: "Great Vibes", cursive; color: var(--title-white);
    font-size: 82px; line-height: 0.9; font-weight: 400;
    text-shadow: 1px 2px 3px rgba(0,0,0,0.25);
  }
  .front__title span { display: block; }
  .front__title .second { padding-left: 118px; }

  .snapframe {
    position: absolute; background: var(--frame-cream);
    border: 1px solid var(--frame-edge);
    box-shadow: 2px 3px 6px rgba(0,0,0,0.45);
    padding: 7px 7px 0;
  }
  .snapframe__photo {
    width: 100%; height: 102px;
    background: radial-gradient(ellipse at 50% 45%, #f6ede6 0%, var(--photo-blush) 55%, var(--photo-shade) 100%);
    box-shadow: inset 0 0 8px rgba(90,60,70,0.35);
  }
  .snapframe__caption {
    font-family: "Great Vibes", cursive; color: var(--caption);
    text-align: center; font-size: 11px; line-height: 22px; white-space: nowrap;
  }
  .snapframe--a { left: 16px;  top: 206px; width: 92px; height: 132px; transform: rotate(-2deg); }
  .snapframe--b { left: 110px; top: 202px; width: 80px; height: 132px; transform: rotate(2deg); }
  .snapframe--d { left: 412px; top: 206px; width: 82px; height: 130px; transform: rotate(-1deg); }
  .snapframe--e { left: 494px; top: 202px; width: 88px; height: 134px; transform: rotate(3deg); }
  .snapframe--main { left: 189px; top: 196px; width: 222px; height: 168px; padding: 9px 9px 0; }
  .snapframe--main .snapframe__photo { height: 134px; }
  .snapframe--main .snapframe__caption { font-size: 13px; line-height: 25px; }

  .front__footer {
    position: absolute; left: 0; right: 0; top: 412px; text-align: center;
    font-family: "Oswald", sans-serif; font-weight: 300; color: var(--footer-text);
    font-size: 17px; letter-spacing: 4.5px;
  }

  /* ---------- Back ---------- */
  .back {
    position: absolute; left: 606px; top: 0; width: 594px; height: 463px; overflow: hidden;
    background: linear-gradient(180deg, #fafafa 0%, var(--back-paper) 100%);
    border: 1px solid var(--back-line);
    font-family: "Handlee", cursive; color: var(--ink-purple);
  }
  .back__return {
    position: absolute; left: 12px; top: 8px; font-size: 10.5px; line-height: 16px;
    font-style: normal; color: var(--ink-purple-soft);
  }
  .back__stamp {
    position: absolute; left: 490px; top: 22px; width: 50px; height: 70px;
    background: var(--stamp); border: 3px dotted #ffffff; outline: 1px solid var(--back-line);
  }
  .back__flower {
    position: absolute; left: 6px; top: 60px; width: 70px; height: 340px;
    background: linear-gradient(180deg, rgba(var(--flower-peach),0.6) 0%, rgba(var(--flower-peach),0.3) 60%, rgba(var(--flower-peach),0.08) 100%);
    border-radius: 35px 35px 12px 12px;
  }
  .back__message {
    position: absolute; left: 82px; top: 172px; width: 206px; text-align: center;
    font-size: 12.5px; line-height: 22px; white-space: nowrap;
  }
  .back__divider { position: absolute; left: 294px; top: 150px; }
  .back__address {
    position: absolute; left: 340px; top: 220px; width: 220px; text-align: center;
    font-size: 16px; line-height: 24px; font-style: normal; white-space: nowrap;
  }
</style>
</head>
<body>
<main class="postcard">

  <section class="front" aria-label="Postcard front">
    <div class="front__scene" role="img" aria-label="Weathered teal painted wood boards with dark vignette edges"></div>
    <div class="front__keepsake" role="img" aria-label="White ceramic heart with dried hydrangea blossoms"></div>
    <h1 class="front__title"><span>Thank</span><span class="second">You</span></h1>

    <figure class="snapframe snapframe--a">
      <div class="snapframe__photo" role="img" aria-label="Space for a wedding party photo"></div>
      <figcaption class="snapframe__caption">Wedding Party</figcaption>
    </figure>
    <figure class="snapframe snapframe--b">
      <div class="snapframe__photo" role="img" aria-label="Space for a wedding party photo"></div>
      <figcaption class="snapframe__caption">Wedding Party</figcaption>
    </figure>
    <figure class="snapframe snapframe--d">
      <div class="snapframe__photo" role="img" aria-label="Space for a wedding party photo"></div>
      <figcaption class="snapframe__caption">Wedding Party</figcaption>
    </figure>
    <figure class="snapframe snapframe--e">
      <div class="snapframe__photo" role="img" aria-label="Space for a wedding party photo"></div>
      <figcaption class="snapframe__caption">Wedding Party</figcaption>
    </figure>
    <figure class="snapframe snapframe--main">
      <div class="snapframe__photo" role="img" aria-label="Space for the couple's wedding day photo"></div>
      <figcaption class="snapframe__caption">Neil and Vera Bradwick</figcaption>
    </figure>

    <p class="front__footer">BRADWICK WEDDING · JUNE 14, 2014</p>
  </section>

  <section class="back" aria-label="Postcard back">
    <address class="back__return">Bradwick Family<br>123 Any Street<br>Anytown, State 45678</address>
    <div class="back__stamp" role="img" aria-label="Postage stamp"></div>
    <div class="back__flower" role="img" aria-label="Faded peach line drawing of tall wildflowers"></div>

    <p class="back__message">
      A living note can barely express<br>
      how you added to our happiness<br>
      on this magical day.<br>
      We would like to send our sincerest<br>
      thanks for your thoughts,<br>
      your gifts, and your presence<br>
      in our lives!<br>
      ♡ love Neil &amp; Vera
    </p>

    <svg class="back__divider" width="20" height="160" viewBox="0 0 20 160" aria-hidden="true">
      <polyline points="4,10 14,18 4,26" fill="none" stroke="var(--chevron)" stroke-width="1.5"/>
      <polyline points="4,70 14,78 4,86" fill="none" stroke="var(--chevron)" stroke-width="1.5"/>
      <polyline points="4,130 14,138 4,146" fill="none" stroke="var(--chevron)" stroke-width="1.5"/>
    </svg>

    <address class="back__address">Bradwick Wedding Guest<br>123 Any Street<br>Anytown, State 45678</address>
  </section>

</main>
</body>
</html>
```